Redesign of business card for Cedar Ridge Mechanical

We are looking for a new design for our business cards for Cedar Ridge Mechanical. We are a plumbing & HVAC construction company, operating on the West Coast of Canada and USA. Logo attached.
Industry/Entity Type
Construction - Plumbing & HVAC
Contact Information for Business Card
Name, address, phone numbers, email, website address
Look and feel
Each slider illustrates characteristics of the customer's brand and the style your logo design should communicate.

```html
<!DOCTYPE html>
<html lang="en">
<head>
<meta charset="utf-8">
<title>Cedar Ridge Mechanical – Business Card</title>
<link rel="stylesheet" href="https://fonts.googleapis.com/css2?family=Fira+Sans:wght@400;600&display=swap">
<style>
  :root {
    --page-bg: #efebe6;
    --card-frost: #e4ded6;
    --card-frost-edge: #d6cfc5;
    --panel-black: #0c0c0c;
    --crescent-grey: #6f6a62;
    --brand-ink: #2a2826;
    --gold-text: #e4d2b2;
    --soft-text: #d8c8ac;
  }
  * { margin: 0; padding: 0; box-sizing: border-box; }
  html, body {
    width: 1200px; height: 1047px; overflow: hidden;
    background: var(--page-bg);
    font-family: "Fira Sans", Arial, sans-serif;
  }
  .card {
    position: absolute; left: 100px; top: 250px;
    width: 1000px; height: 547px;
    border-radius: 26px; overflow: hidden;
    background: linear-gradient(135deg, var(--card-frost), var(--card-frost-edge));
    box-shadow: 0 10px 30px rgba(0,0,0,0.12);
  }
  .card-shapes { position: absolute; inset: 0; }
  .brand {
    position: absolute; left: 62px; top: 250px;
    display: flex; align-items: center; gap: 16px;
  }
  .brand-mark {
    width: 30px; height: 30px; background: var(--brand-ink);
  }
  .brand-name {
    font-size: 34px; font-weight: 600; color: var(--brand-ink);
    letter-spacing: 0.5px;
  }
  .contact {
    position: absolute; left: 648px; top: 108px;
    color: var(--soft-text);
  }
  .person-name {
    font-size: 33px; font-weight: 600; color: var(--gold-text);
    letter-spacing: 0.5px; line-height: 1.1;
  }
  .person-title { font-size: 24px; margin-top: 6px; }
  .address { font-size: 25px; line-height: 38px; margin-top: 38px; }
  .lines { margin-top: 30px; list-style: none; }
  .lines li {
    font-size: 25px; line-height: 37px;
    display: flex; align-items: center; gap: 8px;
  }
  .lines svg { width: 18px; height: 18px; fill: var(--soft-text); flex: none; }
</style>
</head>
<body>
  <div class="card">
    <svg class="card-shapes" viewBox="0 0 1000 547" preserveAspectRatio="none" aria-hidden="true">
      <path d="M683 0 Q430 273 626 547 L1000 547 L1000 0 Z" fill="var(--crescent-grey)"/>
      <path d="M718 0 Q470 273 638 547 L1000 547 L1000 0 Z" fill="var(--panel-black)"/>
    </svg>

    <div class="brand">
      <span class="brand-mark"></span>
      <span class="brand-name">Cedar Ridge Mechanical</span>
    </div>

    <div class="contact">
      <p class="person-name">DANIEL HAYES</p>
      <p class="person-title">Managing Director</p>
      <p class="address">Your address, City<br>State, Zip 1234</p>
      <ul class="lines">
        <li>
          <svg viewBox="0 0 24 24"><path d="M6.6 10.8a15.1 15.1 0 0 0 6.6 6.6l2.2-2.2a1 1 0 0 1 1-.25 11.4 11.4 0 0 0 3.6.57 1 1 0 0 1 1 1V20a1 1 0 0 1-1 1A17 17 0 0 1 3 4a1 1 0 0 1 1-1h3.5a1 1 0 0 1 1 1c0 1.25.2 2.45.57 3.57a1 1 0 0 1-.25 1z"/></svg>
          123 456 789
        </li>
        <li>
          <svg viewBox="0 0 24 24"><path d="M3 5h18a1 1 0 0 1 1 1v12a1 1 0 0 1-1 1H3a1 1 0 0 1-1-1V6a1 1 0 0 1 1-1zm1 2.2V17h16V7.2l-8 5.3z M4.5 7l7.5 5 7.5-5z"/></svg>
          info@yourmail.com
        </li>
        <li>
          <svg viewBox="0 0 24 24"><path d="M12 2a10 10 0 1 0 0 20 10 10 0 0 0 0-20zm6.9 9h-3a15.6 15.6 0 0 0-1.4-6A8 8 0 0 1 18.9 11zM12 4.1A13.6 13.6 0 0 1 13.9 11h-3.8A13.6 13.6 0 0 1 12 4.1zM9.5 5a15.6 15.6 0 0 0-1.4 6h-3A8 8 0 0 1 9.5 5zM5.1 13h3a15.6 15.6 0 0 0 1.4 6 8 8 0 0 1-4.4-6zM12 19.9A13.6 13.6 0 0 1 10.1 13h3.8A13.6 13.6 0 0 1 12 19.9zm2.5-.9a15.6 15.6 0 0 0 1.4-6h3a8 8 0 0 1-4.4 6z"/></svg>
          www.yourwebsite.com
        </li>
      </ul>
    </div>
  </div>
</body>
</html>
```